Rosko Tamblin

I am a songwriter and would like to include a bio, pictures, discography, CD covers and access to some of my music

Target Market(s)

Music Lovers, songwriters publishers

Coding

Coded - Design and coding required

Number of Pages Required

5+ page

Requirements
Must have
• Pictures of my CD covers, pictures of me and either my Music or links to my music
Nice to have
Should not have
• cartoons

```html
<!DOCTYPE html>
<html lang="en">
<head>
<meta charset="utf-8">
<title>Rosko Tamblin — Songwriter</title>
<link href="https://fonts.googleapis.com/css2?family=Anton&family=Great+Vibes&family=Lato:wght@400;700;900&display=swap" rel="stylesheet">
<style>
  :root {
    --bg: #0d0b0c;
    --bg-alt: #141112;
    --purple: #7b1cf0;
    --white: #ffffff;
    --text: #c9c4c4;
    --muted: #8a8585;
    --ghost: #221f20;
    --fire-a: #ff7a1a;
    --fire-b: #7a1606;
  }
  * { box-sizing: border-box; margin: 0; padding: 0; }
  html, body { width: 1200px; height: 3776px; overflow: hidden; background: var(--bg); }
  body { position: relative; font-family: 'Lato', sans-serif; color: var(--text); }
  .abs { position: absolute; }

  .site-header { position: absolute; top: 0; left: 0; width: 1200px; height: 90px; z-index: 5; }
  .brand { position: absolute; left: 140px; top: 24px; font-family: 'Anton', sans-serif; font-size: 30px; letter-spacing: 2px; color: var(--white); }
  .nav { position: absolute; right: 140px; top: 26px; display: flex; align-items: center; gap: 28px; font-size: 14px; font-weight: 700; color: var(--white); letter-spacing: 1px; }
  .nav .active { color: #d9b3ff; }
  .btn-login { background: var(--purple); padding: 10px 22px; }

  .hero { position: absolute; top: 0; left: 0; width: 1200px; height: 740px;
    background: radial-gradient(ellipse at 25% 75%, var(--fire-a), var(--fire-b) 45%, #1b0603 75%); }
  .hero-shade { position: absolute; inset: 0; background: linear-gradient(180deg, rgba(0,0,0,.1), rgba(0,0,0,.45) 80%, var(--bg)); }
  .hero-portrait { position: absolute; left: 480px; top: 90px; width: 240px; height: 280px; border-radius: 40% 40% 10% 10%; background: linear-gradient(180deg, #7a6f66, #c8c0b8 60%, #e8e4e0); opacity: .55; }
  .hero-title { position: absolute; left: 262px; top: 360px; width: 676px; height: 78px; background: var(--purple); font-weight: 900; font-size: 52px; letter-spacing: 3px; color: var(--white); text-align: center; line-height: 78px; }
  .hero-sub { position: absolute; left: 0; top: 462px; width: 1200px; text-align: center; font-size: 19px; font-weight: 700; color: var(--white); line-height: 28px; }
  .btn-outline { position: absolute; border: 2px solid var(--white); color: var(--white); font-size: 14px; font-weight: 700; letter-spacing: 1px; text-align: center; line-height: 36px; height: 40px; }
  .dots { position: absolute; left: 560px; top: 668px; display: flex; gap: 10px; }
  .dots span { width: 10px; height: 10px; border-radius: 50%; background: #8c7d7a; }
  .dots .on { background: var(--white); }

  .script-title { position: absolute; font-family: 'Great Vibes', cursive; font-size: 76px; color: var(--white); white-space: nowrap; }
  .ghost-title { position: absolute; font-family: 'Anton', sans-serif; font-size: 110px; letter-spacing: 6px; color: var(--ghost); white-space: nowrap; }
  .body-copy { position: absolute; font-size: 14px; line-height: 24px; color: var(--muted); }

  .tile { position: absolute; border: 2px solid #3a3435; }

  .ring { position: absolute; left: 720px; top: 1640px; }
  .cover-feature { position: absolute; left: 710px; top: 1880px; width: 300px; height: 340px; background: linear-gradient(180deg, #1c7a8a, #3e6d7a 60%, #8a5a20); border: 2px solid #3a3435; }
  .btn-music { position: absolute; left: 800px; top: 2010px; width: 120px; height: 40px; background: var(--purple); color: var(--white); font-weight: 900; font-size: 16px; line-height: 40px; text-align: center; }

  .testimonial { position: absolute; left: 0; top: 3120px; width: 1200px; height: 590px; background: #000; }
  .testimonial-photo { position: absolute; left: 0; top: 0; width: 440px; height: 590px; background: radial-gradient(ellipse at 40% 45%, #7a7675, #2a2828 55%, #000 85%); }
  .quote-mark { position: absolute; left: 520px; top: 90px; font-family: Georgia, serif; font-size: 110px; color: var(--purple); line-height: 1; }
  .quote-text { position: absolute; left: 520px; top: 175px; width: 560px; font-size: 15px; line-height: 25px; color: var(--text); }
  .stars { color: var(--white); letter-spacing: 1px; }
  .quote-by { position: absolute; left: 520px; top: 335px; font-size: 14px; font-weight: 900; letter-spacing: 1px; color: var(--white); }
  .arrow { position: absolute; top: 430px; width: 44px; height: 44px; border: 2px solid var(--white); border-radius: 50%; }
  .tag { position: absolute; left: 640px; top: 432px; font-family: 'Anton', sans-serif; font-size: 32px; color: var(--purple); }

  .site-footer { position: absolute; left: 0; top: 3710px; width: 1200px; height: 66px; background: var(--bg-alt); }
  .footer-copy { position: absolute; left: 140px; top: 24px; font-size: 13px; color: var(--muted); }
  .socials { position: absolute; right: 140px; top: 24px; display: flex; gap: 16px; }
  .socials span { width: 16px; height: 16px; border-radius: 50%; background: var(--white); }
</style>
</head>
<body>

<section class="hero">
  <div class="abs" style="inset:0" role="img" aria-label="Photo of a fiery crater glowing orange at night"></div>
  <div class="hero-shade"></div>
  <div class="hero-portrait" role="img" aria-label="Portrait of the songwriter in a white jacket"></div>
  <h1 class="hero-title">ROSKO TAMBLIN</h1>
  <p class="hero-sub">Lorem ipsum dolor sit amet, consectetur adipiscing elit<br>sed do eiusmod tempor incididunt</p>
  <a class="btn-outline" style="left:530px;top:556px;width:140px">GET STARTED</a>
  <div class="dots"><span></span><span class="on"></span><span></span><span></span></div>
</section>

<header class="site-header">
  <div class="brand">ROSKO TAMBLIN</div>
  <nav class="nav">
    <span class="active">BIO</span><span>GALLERY</span><span>DISCOGRAPHY</span><span>CD COVERS</span>
    <span class="btn-login">LOGIN</span>
  </nav>
</header>

<section>
  <h2 class="script-title" style="left:140px;top:805px">Biography</h2>
  <p class="body-copy" style="left:530px;top:830px;width:530px">Rosko Tamblin was born and raised in a small Texas town. He began playing music at the age of eight when his sister returned home from summer camp and asked her parents to buy him a used guitar. His long nights of listening to old country records soon shaped his voice, and the following spring he formed his first band, touring the border towns and learning the craft of telling stories in song.</p>
  <a class="btn-outline" style="left:530px;top:1010px;width:130px">READ MORE</a>
</section>

<section>
  <div class="ghost-title" style="left:230px;top:1150px">DISCOGRAPHY</div>
  <h2 class="script-title" style="left:440px;top:1245px">Discography</h2>
  <div class="tile" style="left:145px;top:1345px;width:215px;height:215px;background:linear-gradient(135deg,#c0309a,#3a7ad0 60%,#e0a020)" role="img" aria-label="Album cover with a guitarist in bright colours"></div>
  <div class="tile" style="left:378px;top:1345px;width:215px;height:215px;background:linear-gradient(160deg,#e8d070,#c84a1a 55%,#3a2a1a)" role="img" aria-label="Album cover by Clay Harlan"></div>
  <div class="tile" style="left:611px;top:1345px;width:215px;height:215px;background:linear-gradient(180deg,#3a3e5a,#6a6a8a 45%,#1a1a2a)" role="img" aria-label="Album cover with a stormy sky and lightning"></div>
  <div class="tile" style="left:844px;top:1345px;width:215px;height:215px;background:linear-gradient(180deg,#2a2a2a,#b8651e 55%,#5a3010)" role="img" aria-label="Album cover titled Harbor Lights Home"></div>
</section>

<section>
  <div class="ghost-title" style="left:0;top:1670px">CD COVERS</div>
  <h2 class="script-title" style="left:140px;top:1760px">CD Covers</h2>
  <p class="body-copy" style="left:140px;top:1890px;width:400px">Lorem ipsum dolor sit amet, consectetur adipiscing elit, sed do eiusmod tempor incididunt ut labore et dolore magna aliqua ipsum suspendisse ultrices gravida. Risus commodo viverra maecenas accumsan lacus vel facilisis. Lorem ipsum dolor sit amet, consectetur adipiscing elit, sed do eiusmod tempor incididunt ut labore et dolore magna aliqua ipsum suspendisse ultrices gravida commodo viverra maecenas.</p>
  <a class="btn-outline" style="left:140px;top:2100px;width:130px">READ MORE</a>
  <svg class="ring" width="480" height="620" viewBox="0 0 480 620">
    <defs><linearGradient id="ringGrad" x1="0" y1="0" x2="1" y2="1"><stop offset="0" stop-color="#6a10e8"/><stop offset="1" stop-color="#a020f0"/></linearGradient></defs>
    <circle cx="320" cy="310" r="225" fill="none" stroke="url(#ringGrad)" stroke-width="110"/>
  </svg>
  <div class="cover-feature" role="img" aria-label="CD cover titled Harbor Lights Home with a ship on stormy seas"></div>
  <div class="btn-music">MY MUSIC</div>
</section>

<section>
  <div class="ghost-title" style="left:460px;top:2300px">GALLERY</div>
  <h2 class="script-title" style="left:445px;top:2345px">My Gallery</h2>
  <div class="tile" style="left:145px;top:2510px;width:295px;height:250px;background:linear-gradient(180deg,#3a5a2a,#b09070 60%,#6a5a40)" role="img" aria-label="Photo of the songwriter in a cowboy hat outdoors"></div>
  <div class="tile" style="left:455px;top:2510px;width:295px;height:250px;background:linear-gradient(180deg,#6a3a1a,#c8b8a8 60%,#8a6a4a)" role="img" aria-label="Photo of the songwriter in a white shirt"></div>
  <div class="tile" style="left:765px;top:2510px;width:295px;height:250px;background:linear-gradient(160deg,#e0dcd8,#b0a8c8 60%,#d8c0c0)" role="img" aria-label="Album cover titled Porchlight Years"></div>
  <div class="tile" style="left:145px;top:2780px;width:295px;height:250px;background:linear-gradient(160deg,#e8d070,#c84a1a 55%,#3a2a1a)" role="img" aria-label="Album cover by Clay Harlan"></div>
  <div class="tile" style="left:455px;top:2780px;width:295px;height:250px;background:linear-gradient(180deg,#2a2a2a,#b8651e 55%,#5a3010)" role="img" aria-label="Album cover titled Harbor Lights Home"></div>
  <div class="tile" style="left:765px;top:2780px;width:295px;height:250px;background:linear-gradient(180deg,#3a3e5a,#6a6a8a 45%,#1a1a2a)" role="img" aria-label="Album art with a stormy sky and a silhouette"></div>
</section>

<section class="testimonial">
  <div class="testimonial-photo" role="img" aria-label="Black and white photo of the songwriter playing guitar"></div>
  <div class="quote-mark">&ldquo;</div>
  <p class="quote-text">If you are looking for superb song writing and composition then Rosko is your guy. Not only is he truly a professional, he has a unique style and extremely engaging storytelling. I am amazed every time!!! <span class="stars">★★★★★★★★★</span> I have spent a long time listening to his records and each new song feels like a conversation with an old friend.</p>
  <div class="quote-by">– AWARD NOMINATED SONGWRITER VOCALS</div>
  <svg class="arrow" style="left:520px" viewBox="0 0 44 44"><path d="M25 14 L17 22 L25 30" stroke="#fff" stroke-width="2.5" fill="none"/></svg>
  <svg class="arrow" style="left:576px" viewBox="0 0 44 44"><path d="M19 14 L27 22 L19 30" stroke="#fff" stroke-width="2.5" fill="none"/></svg>
  <div class="tag">$ US</div>
</section>

<footer class="site-footer">
  <div class="footer-copy">© 2020 Rosko Tamblin All Rights Reserved. | Privacy Policy | Terms and Use</div>
  <div class="socials"><span></span><span></span><span></span></div>
</footer>

</body>
</html>
```